Mobile Fitness snd Therapy Business Card Design

I need a business card designed for my mobile fitness and therapy business.

Please view the images that I have uploaded. I like the simplicity of the design that I have attached. I adapted it with my information

Target Market(s)

Those seeking personal training, injury rehabilitation or massage therapy.

Industry/Entity Type

Business

Contact Information for Business Card

Derek Fulham - MSc, CAT(C), RMT, CSCS, Pn2
e-mail: derek@vantrelo.com
website: www.vantrelo.com
instagram: @derek_fulham

Font styles to use
Sans Serif

Colors
3176b5
0355a3

Requirements
Must have
• "Contact us to receive a FREE assessment"
• Services offered:
• Personal Training
• Golf Fitness
• Injury Rehab
• Massage Therapy
• Yoga
Nice to have
• Consistent colours with brand
• - Dark Blue: #232837
• - Blue: #5096f0
• Consistent look/feel with the website: www.vantrelo.com

```html
<!DOCTYPE html>
<html lang="en">
<head>
<meta charset="utf-8">
<title>Vantrelo Business Card</title>
<link href="https://fonts.googleapis.com/css2?family=Roboto:wght@400;500;700&display=swap" rel="stylesheet">
<style>
  :root {
    --bg: #e3e3e3;
    --brand-blue: #5096f0;
    --dark-blue: #232837;
    --white: #ffffff;
    --text: #1f2330;
  }
  * { box-sizing: border-box; margin: 0; padding: 0; }
  html, body { width: 1200px; height: 852px; overflow: hidden; }
  body {
    background: var(--bg);
    font-family: "Roboto", Arial, sans-serif;
    display: flex;
    align-items: center;
    justify-content: center;
    gap: 60px;
  }
  .card {
    position: relative;
    width: 520px;
    height: 297px;
    border-radius: 24px;
    overflow: hidden;
    box-shadow: 0 6px 18px rgba(0,0,0,0.18);
  }
  /* Front */
  .card-front {
    background: var(--brand-blue);
    color: var(--white);
    display: flex;
    flex-direction: column;
    align-items: center;
    justify-content: center;
  }
  .brand-name {
    font-size: 58px;
    font-weight: 500;
    letter-spacing: 6px;
    line-height: 1;
  }
  .brand-tagline {
    margin-top: 10px;
    font-size: 15px;
    font-weight: 500;
    letter-spacing: 4px;
  }
  /* Back */
  .card-back { background: var(--white); color: var(--text); }
  .edge-band {
    position: absolute;
    width: 22px;
    background: var(--dark-blue);
  }
  .edge-band-left { left: 0; top: 120px; bottom: 0; }
  .edge-band-right { right: 0; top: 0; height: 178px; }
  .contact-block {
    position: absolute;
    left: 48px;
    top: 118px;
  }
  .person-name {
    font-size: 24px;
    font-weight: 700;
    letter-spacing: 0.3px;
    color: var(--text);
  }
  .credentials {
    margin-top: 3px;
    font-size: 13px;
    color: var(--brand-blue);
  }
  .contact-list { list-style: none; margin-top: 12px; }
  .contact-list li {
    display: flex;
    align-items: center;
    gap: 8px;
    font-size: 15px;
    line-height: 20px;
  }
  .contact-list svg { width: 14px; height: 14px; flex: none; }
  .accent { color: var(--brand-blue); }
  .divider {
    position: absolute;
    left: 290px;
    top: 36px;
    width: 1px;
    height: 140px;
    background: var(--brand-blue);
  }
  .services {
    position: absolute;
    left: 318px;
    top: 30px;
  }
  .services-title {
    font-size: 15px;
    font-weight: 700;
    color: var(--brand-blue);
    margin-bottom: 2px;
  }
  .services-list { list-style: none; }
  .services-list li {
    font-size: 15px;
    line-height: 19px;
    padding-left: 14px;
    position: relative;
  }
  .services-list li::before {
    content: "»";
    position: absolute;
    left: 0;
    color: var(--brand-blue);
  }
  .cta {
    position: absolute;
    left: 0; right: 0;
    bottom: 20px;
    display: flex;
    align-items: center;
    justify-content: center;
    gap: 12px;
    font-size: 15px;
  }
  .cta-rule { width: 46px; height: 2px; background: var(--brand-blue); }
</style>
</head>
<body>
  <section class="card card-front">
    <div class="brand-name">VANTRELO</div>
    <div class="brand-tagline">NUTRITION - FITNESS - HEALTH</div>
  </section>

  <section class="card card-back">
    <div class="edge-band edge-band-left"></div>
    <div class="edge-band edge-band-right"></div>

    <div class="contact-block">
      <h1 class="person-name">DEREK FULHAM</h1>
      <p class="credentials">MSc, CAT(C), RMT, CSCS, Pn2</p>
      <ul class="contact-list">
        <li>
          <svg viewBox="0 0 16 16" fill="none" stroke="#5096f0" stroke-width="1.5"><circle cx="8" cy="8" r="6.8"/><path d="M5.6 4.8l1.2 1.6-.7.9c.5 1 1.3 1.8 2.3 2.3l.9-.7 1.6 1.2-.7 1.1c-2.6-.3-4.9-2.6-5.2-5.2z" fill="#5096f0" stroke="none"/></svg>
          250-555-0147
        </li>
        <li>
          <svg viewBox="0 0 16 16" fill="none" stroke="#5096f0" stroke-width="1.5"><rect x="1.5" y="3.5" width="13" height="9" rx="1"/><path d="M2 4l6 5 6-5"/></svg>
          derek@vantrelo.com
        </li>
        <li>
          <svg viewBox="0 0 16 16" fill="none" stroke="#5096f0" stroke-width="1.3"><circle cx="8" cy="8" r="6.5"/><ellipse cx="8" cy="8" rx="3" ry="6.5"/><path d="M1.5 8h13M2.5 5h11M2.5 11h11"/></svg>
          www.<span class="accent">vantrelo</span>.com
        </li>
        <li>
          <svg viewBox="0 0 16 16" fill="none" stroke="#5096f0" stroke-width="1.5"><circle cx="8" cy="8" r="6.5"/></svg>
          @derek_fulham
        </li>
      </ul>
    </div>

    <div class="divider"></div>

    <div class="services">
      <h2 class="services-title">Services offered:</h2>
      <ul class="services-list">
        <li>Personal Training</li>
        <li>Group Training</li>
        <li>Nutrition Coaching</li>
        <li>Golf Fitness</li>
        <li>Injury Rehabilitation</li>
        <li>Massage Therapy</li>
        <li>Yoga</li>
      </ul>
    </div>

    <p class="cta">
      <span class="cta-rule"></span>
      <span>Contact us to receive a <span class="accent">FREE</span> assessment</span>
      <span class="cta-rule"></span>
    </p>
  </section>
</body>
</html>
```